Corporate Design für ein Verein zur Förderung der Kommunikation und Inklusion
Zielgruppe
Der Verein richtet sich an alle Menschen mit und ohne Behinderung die sich am Thema Inklusion beteiligen möchten. Wir möchten in erster Linie die Kommunikation in diesem Bereich fördern.
Aufgabenstellung
Der Veinein hat 2 Arten der Darstellung des Namen in kurz und lang.
Sprachverbund - Verein zur Stärkung von Austausch und Teilhabe für ein eigenständiges Dasein e. V.
Sprachverbund e. V.
Die Pride Farben und evtl. andere Symbole wie Sprechblasen oder Menschen könnten die Inklusion und den Austausch symbolisieren.
Gut lesbar auch für Sehbehinderte ist von vorteil aber ein modernes und ansprechendes Auftreten ohne einzige Beschränkung nur auf Sehbehinderungen.
Evtl. auch ein Logo das Fühlbar auf Visitenkarten durckbar ist. Jedoch eher eine Alternative als der Schwerpunkt auch durch Kosten hierfür.

```html
<!DOCTYPE html>
<html lang="de">
<head>
<meta charset="utf-8">
<title>Sprachverbund – Visitenkarte</title>
<link rel="stylesheet" href="https://fonts.googleapis.com/css2?family=Montserrat:wght@400;600;700&display=swap">
<style>
  :root {
    --page-bg: #ffffff;
    --card-front: #efefef;
    --ink: #1c1c1c;
    --violet: #4a1160;
    --night: #101a36;
    --white: #ffffff;
    --soft-white: rgba(255,255,255,0.05);
    --r1: #e8412c;
    --r2: #e0a21a;
    --r3: #3a9a5a;
    --r4: #2f6fe6;
    --r5: #6a3fd0;
    --r6: #9c2fa6;
  }
  * { box-sizing: border-box; margin: 0; padding: 0; }
  html, body {
    width: 1200px; height: 1200px; overflow: hidden;
    background: var(--page-bg);
    font-family: "Montserrat", sans-serif;
  }
  .canvas { position: relative; width: 1200px; height: 1200px; }
  .card {
    position: absolute;
    width: 663px; height: 393px;
    border-radius: 26px;
    overflow: hidden;
  }
  .card-front {
    left: 260px; top: 163px;
    background: var(--card-front);
    display: flex; flex-direction: column; align-items: center; justify-content: center;
    gap: 26px;
  }
  .front-mark {
    width: 96px; height: 96px;
    border-radius: 18px;
    background: var(--violet);
  }
  .front-name {
    font-weight: 700; font-size: 26px; letter-spacing: 0.07em;
    color: var(--ink);
  }
  .card-back {
    left: 272px; top: 644px;
    background: linear-gradient(90deg, var(--violet) 5%, #2a1448 45%, var(--night) 100%);
    color: var(--white);
  }
  .back-name {
    position: absolute; left: 41px; top: 34px;
    display: flex; align-items: center; gap: 10px;
    font-weight: 700; font-size: 22px; letter-spacing: 0.05em;
  }
  .back-dot { width: 18px; height: 18px; background: var(--white); }
  .back-watermark {
    position: absolute; left: 320px; top: 90px;
    width: 190px; height: 190px;
    border-radius: 40px;
    background: var(--soft-white);
  }
  .person {
    position: absolute; left: 67px; top: 188px; width: 200px;
    text-align: center;
  }
  .person-name { font-weight: 400; font-size: 20px; letter-spacing: 0.06em; }
  .person-role { font-weight: 700; font-size: 20px; letter-spacing: 0.08em; margin-top: 2px; }
  .contact {
    position: absolute; left: 362px; top: 190px;
    list-style: none;
    font-weight: 400; font-size: 16px; letter-spacing: 0.06em; line-height: 22.3px;
    white-space: nowrap;
  }
  .rainbow-rule {
    position: absolute; left: 41px; top: 358px;
    width: 582px; height: 4px; border-radius: 2px;
    background: linear-gradient(90deg, var(--r1), var(--r2) 25%, var(--r3) 45%, var(--r4) 70%, var(--r5) 88%, var(--r6));
  }
</style>
</head>
<body>
<main class="canvas">
  <section class="card card-front">
    <div class="front-mark"></div>
    <div class="front-name">SPRACHVERBUND</div>
  </section>

  <section class="card card-back">
    <div class="back-name"><span class="back-dot"></span>SPRACHVERBUND</div>
    <div class="back-watermark"></div>
    <div class="person">
      <div class="person-name">Lena Brandt</div>
      <div class="person-role">CEO</div>
    </div>
    <ul class="contact">
      <li>27 Lindenweg, Kassel, Hessen</li>
      <li>www.sprachverbund.de</li>
      <li>hallo@sprachverbund.de</li>
      <li>l.brandt@sprachverbund.de</li>
      <li>+49 561 204 719</li>
      <li>+49 561 884 302</li>
    </ul>
    <div class="rainbow-rule"></div>
  </section>
</main>
</body>
</html>
```